New Business Card Design

We would like to refresh our business cards and make them look better. We are an IT company specialising in Cloud Services, IT Managed Services, software and hardware. I have attached a PSD of our current design. Also attached our logo.
Updates

I have uploaded all new logos in EPS format.

Can you please edit all designs to include a job title for Marcus Hollis, eg. General Manager

Industry/Entity Type

Software

Colors
ffffff

Requirements
Must have
• Please use white background.
Should not have
• Black background

```html
<!DOCTYPE html>
<html lang="en">
<head>
<meta charset="utf-8">
<title>Clarity Systems – Business Card</title>
<link rel="stylesheet" href="https://fonts.googleapis.com/css2?family=Questrial&display=swap">
<style>
  :root {
    --brand-red: #ed1c24;
    --soft-red: #f4606a;
    --name-gold: #f2a900;
    --text-dark: #231f20;
    --text-grey: #7a7c80;
    --line-dark: #3a3f4a;
    --line-grey: #a7a9ac;
    --paper: #ffffff;
    --canvas: #ffffff;
  }
  * { margin: 0; padding: 0; box-sizing: border-box; }
  html, body { width: 1200px; height: 377px; overflow: hidden; background: var(--canvas); }
  body { position: relative; font-family: "Questrial", "Century Gothic", sans-serif; }

  .card { position: absolute; top: 30px; width: 568px; height: 317px; overflow: hidden; }
  .card--front { left: 16px; background: var(--brand-red); }
  .card--back { left: 615px; background: var(--paper); border: 1px solid #e6e6e6; }

  /* Front */
  .front-ornament {
    position: absolute; left: 0; bottom: 0; width: 200px; height: 170px;
    background: radial-gradient(ellipse at 30% 70%, rgba(255,255,255,0.28), rgba(255,255,255,0) 70%);
  }
  .front-brand { position: absolute; left: 66px; top: 96px; display: flex; align-items: center; gap: 18px; }
  .front-brand__mark { width: 68px; height: 68px; border-radius: 50%; background: var(--paper); }
  .front-brand__name { color: var(--paper); font-size: 38px; letter-spacing: 7px; white-space: nowrap; }

  .services { position: absolute; display: flex; list-style: none; font-size: 13.5px; }
  .services li { display: flex; align-items: center; margin-right: 17px; }
  .services li::before { content: ""; width: 6px; height: 6px; border-radius: 50%; margin-right: 7px; }
  .services li:last-child { margin-right: 0; }
  .card--front .services { left: 68px; bottom: 13px; color: var(--paper); }
  .card--front .services li::before { background: var(--paper); }
  .card--back .services { left: 0; right: 0; bottom: 13px; justify-content: center; color: var(--text-dark); }
  .card--back .services li::before { background: var(--brand-red); }

  /* Back */
  .back-brand { position: absolute; left: 32px; top: 44px; display: flex; align-items: center; gap: 9px; }
  .back-brand__mark { width: 22px; height: 22px; border-radius: 50%; background: var(--brand-red); }
  .back-brand__name { color: var(--text-dark); font-size: 19px; letter-spacing: 2px; }

  .person { position: absolute; right: 25px; top: 44px; text-align: right; }
  .person__name { font-size: 24px; line-height: 1; padding-bottom: 5px; border-bottom: 1px solid var(--line-grey); width: 176px; }
  .person__first { color: var(--name-gold); }
  .person__last { color: var(--brand-red); }
  .person__title { font-size: 11.5px; color: var(--text-grey); margin-top: 3px; }

  .contact { position: absolute; right: 25px; text-align: right; }
  .contact--phones { top: 128px; }
  .phone { display: flex; align-items: center; justify-content: flex-end; font-size: 19px; color: var(--text-grey); height: 28px; }
  .phone__badge { width: 19px; height: 19px; margin-right: 10px; }
  .contact__email { top: 192px; font-size: 18px; color: var(--text-dark); }
  .contact__web { top: 235px; font-size: 18px; color: var(--text-grey); }

  .rule { position: absolute; top: 276px; height: 2px; }
  .rule--red { left: 22px; width: 374px; background: var(--brand-red); }
  .rule--dark { left: 400px; width: 102px; background: var(--line-dark); }
  .rule--grey { left: 504px; width: 37px; background: var(--line-grey); }
</style>
</head>
<body>

<section class="card card--front">
  <div class="front-ornament" role="img" aria-label="Soft floral flourish decoration in light red tones"></div>
  <div class="front-brand">
    <span class="front-brand__mark"></span>
    <span class="front-brand__name">clarity systems</span>
  </div>
  <ul class="services">
    <li>Cloud Services</li>
    <li>It Managed Services</li>
    <li>Software</li>
    <li>Hardware</li>
  </ul>
</section>

<section class="card card--back">
  <div class="back-brand">
    <span class="back-brand__mark"></span>
    <span class="back-brand__name">clarity systems</span>
  </div>

  <div class="person">
    <div class="person__name"><span class="person__first">Marcus</span><span class="person__last">Hollis</span></div>
    <div class="person__title">General Manager</div>
  </div>

  <div class="contact contact--phones">
    <div class="phone">
      <svg class="phone__badge" viewBox="0 0 20 20" aria-hidden="true">
        <circle cx="10" cy="10" r="10" fill="#ed1c24"/>
        <text x="10" y="14.5" text-anchor="middle" font-size="13" font-family="Arial, sans-serif" font-weight="bold" fill="#fff">M</text>
      </svg>
      <span>07 3555 0148</span>
    </div>
    <div class="phone">
      <svg class="phone__badge" viewBox="0 0 20 20" aria-hidden="true">
        <circle cx="10" cy="10" r="10" fill="#ed1c24"/>
        <text x="10" y="14.5" text-anchor="middle" font-size="13" font-family="Arial, sans-serif" font-weight="bold" fill="#fff">P</text>
      </svg>
      <span>0400 555 217</span>
    </div>
  </div>

  <div class="contact contact__email">mhollis@claritysys.com.au</div>
  <div class="contact contact__web">www.claritysys.com.au</div>

  <span class="rule rule--red"></span>
  <span class="rule rule--dark"></span>
  <span class="rule rule--grey"></span>

  <ul class="services">
    <li>Cloud Services</li>
    <li>It Managed Services</li>
    <li>Software</li>
    <li>Hardware</li>
  </ul>
</section>

</body>
</html>
```